Seeking funky, innovative business cards

I am looking to refresh our current business cards to something more engaging, visual and impactful. We are a management consultancy firm, see website (www.larkstone-partners.com.au). I've included our colour scheme, sample of the slides we use and our old business cards. We would like our cards to have icons. The card should display:- Name- Title- Mobile number- Address- Email address- Website - Company logo- Our purpose statement "We shape workplaces people are proud to join"

Contact Information for Business Card

Brennan Ulfsson
Consultant
0468 927 341
Level 3, 218 Wexley Street, Melbourne 3000
brennan@larkstone-partners.com.au
www.larkstone-partners.com.au

Purpose statement "We shape workplaces people are proud to join"
LOGO available in google images

Font styles to use
Other font styles liked:
• Open Sans Light, Bebas Neue (open to other cool foints)

Colors
ffc214
5c5c5c
f5f5f5
fefefe

Requirements
Must have
• - Name
• - Title
• - Mobile number
• - Address
• - Email address
• - Website
• - Company logo
• - Our purpose statement "We shape workplaces people are proud to join"
Nice to have
• - Icons
• - Colour (see our colour scheme"

```html
<!DOCTYPE html>
<html lang="en">
<head>
<meta charset="utf-8">
<title>Larkstone Partners — Business Card</title>
<link rel="stylesheet" href="https://fonts.googleapis.com/css2?family=Open+Sans:ital,wght@0,300;0,400;0,600;1,400&display=swap">
<style>
  :root {
    --brand-yellow: #ffc214;
    --brand-amber: #f2a516;
    --ink: #5c5c5c;
    --ink-dark: #3f4042;
    --paper: #fefefe;
    --paper-shade: #f5f5f5;
    --stage: #e9e9e9;
    --tagline-blue: #3f78b4;
  }
  * { box-sizing: border-box; margin: 0; padding: 0; }
  html, body { width: 1200px; height: 943px; overflow: hidden; }
  body {
    background: var(--stage);
    font-family: "Open Sans", sans-serif;
    color: var(--ink);
    display: flex;
    align-items: center;
    justify-content: center;
    gap: 50px;
  }
  .card {
    position: relative;
    width: 540px;
    height: 330px;
    overflow: hidden;
    box-shadow: 0 10px 28px rgba(0,0,0,.18);
  }

  /* Front */
  .card--front {
    background: linear-gradient(160deg, var(--paper) 0%, var(--paper-shade) 100%);
  }
  .brand {
    position: absolute;
    left: 38px;
    top: 70px;
    display: flex;
    align-items: center;
    gap: 10px;
  }
  .brand__dot {
    width: 14px; height: 14px;
    border-radius: 50%;
    background: var(--brand-yellow);
  }
  .brand__name {
    font-weight: 300;
    font-size: 36px;
    line-height: 1.05;
    color: var(--ink);
    letter-spacing: -0.5px;
  }
  .person {
    position: absolute;
    left: 280px;
    top: 62px;
  }
  .person__name {
    font-size: 21px;
    font-weight: 400;
    text-transform: uppercase;
    letter-spacing: .5px;
    color: var(--ink-dark);
    white-space: nowrap;
  }
  .person__title {
    font-style: italic;
    font-size: 15px;
    color: var(--brand-amber);
    margin-top: 2px;
  }
  .contacts {
    list-style: none;
    margin-top: 12px;
    font-size: 12.5px;
    line-height: 1.35;
  }
  .contacts li {
    display: flex;
    align-items: flex-start;
    gap: 9px;
    margin-bottom: 5px;
  }
  .contacts svg { flex: none; width: 13px; height: 13px; margin-top: 2px; }
  .edge-band {
    position: absolute;
    left: 0; right: 0; bottom: 0;
    height: 38px;
    display: flex;
  }
  .edge-band__yellow { flex: 56; background: linear-gradient(90deg, var(--brand-yellow), var(--brand-amber)); }
  .edge-band__grey { flex: 44; background: linear-gradient(90deg, #6a6b6d, var(--ink-dark)); }

  /* Back */
  .card--back {
    background: radial-gradient(circle at 40% 30%, #ffd54a 0%, var(--brand-yellow) 45%, var(--brand-amber) 100%);
    display: flex;
    flex-direction: column;
    align-items: center;
    justify-content: center;
  }
  .card--back .brand {
    position: static;
  }
  .card--back .brand__dot { background: var(--paper); }
  .card--back .brand__name { font-size: 44px; }
  .tagline {
    margin-top: 18px;
    font-size: 14px;
    font-weight: 600;
    color: var(--tagline-blue);
  }
</style>
</head>
<body>

  <section class="card card--front" aria-label="Business card front">
    <div class="brand">
      <span class="brand__dot"></span>
      <span class="brand__name">Larkstone<br>Partners</span>
    </div>

    <div class="person">
      <h1 class="person__name">Brennan Ulfsson</h1>
      <p class="person__title">Consultant</p>
      <ul class="contacts">
        <li>
          <svg viewBox="0 0 16 16" aria-hidden="true"><rect width="16" height="16" rx="3" fill="#ffc214"/><path d="M5 3.5l1.6 2.3-1 1.1a6 6 0 0 0 3.5 3.5l1.1-1 2.3 1.6-.8 1.5C8 12.8 3.2 8 3.5 4.3z" fill="#fff"/></svg>
          <span>0468 927 341</span>
        </li>
        <li>
          <svg viewBox="0 0 16 16" aria-hidden="true"><rect width="16" height="16" rx="3" fill="#ffc214"/><rect x="3" y="4.5" width="10" height="7" fill="#fff"/><path d="M3 4.5l5 4 5-4" stroke="#ffc214" stroke-width="1" fill="none"/></svg>
          <span>brennan@larkstone-partners.com.au</span>
        </li>
        <li>
          <svg viewBox="0 0 16 16" aria-hidden="true"><circle cx="8" cy="8" r="7.5" fill="#ffc214"/><g stroke="#fff" stroke-width="1" fill="none"><circle cx="8" cy="8" r="5"/><ellipse cx="8" cy="8" rx="2.2" ry="5"/><path d="M3 8h10"/></g></svg>
          <span>www.larkstone-partners.com.au</span>
        </li>
        <li>
          <svg viewBox="0 0 16 16" aria-hidden="true"><path d="M8 1a5 5 0 0 1 5 5c0 4-5 9-5 9S3 10 3 6a5 5 0 0 1 5-5z" fill="#ffc214"/><circle cx="8" cy="6" r="1.8" fill="#fff"/></svg>
          <span>Level 3, 218 Wexley Street,<br>Melbourne 3000</span>
        </li>
      </ul>
    </div>

    <div class="edge-band" aria-hidden="true">
      <div class="edge-band__yellow"></div>
      <div class="edge-band__grey"></div>
    </div>
  </section>

  <section class="card card--back" aria-label="Business card back">
    <div class="brand">
      <span class="brand__dot"></span>
      <span class="brand__name">Larkstone Partners</span>
    </div>
    <p class="tagline">We shape workplaces people are proud to join</p>
  </section>

</body>
</html>
```